Parcelwise HQ letterhead and envelope

Design a formal (8.5x11) letterhead and envelope for sales outreach and legal matters. Using design input from https://www.parcelwisehq.example/ and the attached documents.

Industry/Entity Type

Software Service

Requirements
Must have
• These 4 hex colors are our official colors:
• #355c98 [blue]
• #1eb1a2 [teal]
• #fdba12 [gold]
• #f1653b [orange]
• So no other colors besides these should be used.

```html
<!DOCTYPE html>
<html lang="en">
<head>
<meta charset="utf-8">
<title>Parcelwise HQ Letterhead</title>
<link href="https://fonts.googleapis.com/css2?family=Lato:wght@300;400;700&family=Roboto:wght@400&family=Yellowtail&display=swap" rel="stylesheet">
<style>
  :root {
    --blue: #355c98;
    --teal: #1eb1a2;
    --gold: #fdba12;
    --orange: #f1653b;
    --ink: #4a4a4a;
    --paper: #ffffff;
  }
  * { margin: 0; padding: 0; box-sizing: border-box; }
  html, body { width: 996px; height: 1200px; overflow: hidden; background: var(--paper); }
  .letterhead { position: relative; width: 996px; height: 1200px; background: var(--paper); font-family: "Lato", sans-serif; color: var(--ink); }

  .brand { position: absolute; left: 70px; top: 28px; display: flex; align-items: center; gap: 14px; }
  .brand-mark { width: 50px; height: 50px; border: 4px solid var(--blue); border-radius: 50%; }
  .brand-name { font-family: "Lato", sans-serif; font-weight: 300; font-size: 46px; color: var(--blue); letter-spacing: 0.5px; }

  .rule { position: absolute; top: 106px; height: 3px; background: var(--blue); }
  .rule-left { left: 0; width: 632px; }
  .rule-right { left: 922px; width: 74px; }
  .web { position: absolute; left: 648px; top: 94px; width: 266px; text-align: center; font-family: "Roboto", sans-serif; font-size: 16px; letter-spacing: 3.2px; color: var(--blue); }

  .decor { position: absolute; border-radius: 50%; opacity: 0.18; }
  .decor-bulb { left: 906px; top: 232px; width: 80px; height: 84px; background: radial-gradient(circle, var(--orange), transparent 70%); }
  .decor-bolt-gold { left: 200px; top: 196px; width: 40px; height: 92px; background: linear-gradient(var(--gold), transparent); }
  .decor-play { left: 540px; top: 188px; width: 58px; height: 46px; background: radial-gradient(circle, var(--orange), transparent 70%); }
  .decor-lock { left: 428px; top: 340px; width: 52px; height: 62px; background: radial-gradient(circle, var(--gold), transparent 70%); }
  .decor-person { left: 716px; top: 760px; width: 100px; height: 94px; background: radial-gradient(circle, var(--orange), transparent 70%); }
  .decor-bolt-teal { left: 912px; top: 942px; width: 52px; height: 110px; background: linear-gradient(var(--teal), transparent); }
  .pin { position: absolute; left: 944px; top: 428px; width: 40px; height: 48px; }

  .letter { position: absolute; left: 73px; top: 370px; width: 854px; }
  .salutation { font-weight: 700; font-size: 18px; color: var(--blue); margin-bottom: 22px; }
  .body-copy p { font-size: 17.6px; line-height: 26px; margin-bottom: 22px; }
  .closing { font-size: 20px; color: #222; margin-top: 8px; }
  .signature { font-family: "Yellowtail", cursive; font-size: 40px; color: var(--blue); margin-top: 0; }

  .contact { position: absolute; left: 66px; top: 1158px; width: 900px; display: flex; align-items: center; gap: 10px; font-family: "Roboto", sans-serif; font-size: 15px; color: #333; white-space: nowrap; }
  .contact-item { display: flex; align-items: center; gap: 6px; }
  .contact-item svg { width: 15px; height: 15px; }
  .contact-divider { width: 1px; height: 16px; background: #bbb; }
</style>
</head>
<body>
<main class="letterhead">
  <header>
    <div class="brand">
      <span class="brand-mark"></span>
      <span class="brand-name">Parcelwise HQ</span>
    </div>
    <div class="rule rule-left"></div>
    <div class="web">www.parcelwisehq.example</div>
    <div class="rule rule-right"></div>
  </header>

  <div class="decor decor-bulb" role="img" aria-label="Faint orange line icon of a light bulb"></div>
  <div class="decor decor-bolt-gold" role="img" aria-label="Faint gold line icon of a lightning bolt"></div>
  <div class="decor decor-play" role="img" aria-label="Faint orange line icon of a play triangle"></div>
  <div class="decor decor-lock" role="img" aria-label="Faint gold line icon of a padlock"></div>
  <div class="decor decor-person" role="img" aria-label="Faint orange line icon of a user profile"></div>
  <div class="decor decor-bolt-teal" role="img" aria-label="Faint teal line icon of a lightning bolt"></div>
  <svg class="pin" viewBox="0 0 40 48" aria-hidden="true">
    <path d="M20 46 C10 32 4 24 4 17 A16 16 0 0 1 36 17 C36 24 30 32 20 46 Z" fill="none" stroke="var(--blue)" stroke-width="1.5" opacity="0.45"/>
    <circle cx="20" cy="17" r="5.5" fill="none" stroke="var(--blue)" stroke-width="1.5" opacity="0.45"/>
  </svg>

  <section class="letter">
    <p class="salutation">Dear Mr. Lorem,</p>
    <div class="body-copy">
      <p>Lorem ipsum dolor sit amet, consectetuer adipiscing elit, sed diam nonummy nibh euismod tincidunt ut laoreet dolore magna aliquam erat volutpat. Ut wisi enim ad minim veniam, quis nostrud exerci tation ullamcorper suscipit lobortis nisl ut aliquip ex ea commodo consequat. Duis autem vel eum iriure dolor in hendiusto odio dignissim qui blandit praesent luptatum zzril delenit augue duis dolore te feugait nulla facilisi.</p>
      <p>Lorem ipsum dolor sit amet, consectetuer adipiscing elit, sed diam nonummy nibh euismod tincidunt ut laoreet dolore magna aliquam erat volutpat. Ut wisi enim ad minim veniam, quis nostrud exerci tation ullamcorper suscipit lobortis nisl ut aliquip ex ea commodo consequat. Duis autem vel eum iriure dolor in hendiusto odio dignissim qui blandit praesent luptatum zzril delenit augue duis dolore te feugait nulla facilisi.</p>
      <p>Lorem ipsum dolor sit amet, consectetuer adipiscing elit, sed diam nonummy nibh euismod tincidunt ut laoreet dolore magna aliquam erat volutpat. Ut wisi enim ad minim veniam, quis nostrud exerci tation ullamcorper suscipit lobortis nisl ut aliquip ex ea commodo consequat. Duis autem vel eum iriure dolor in hendiusto odio dignissim qui blandit praesent luptatum zzril delenit augue duis dolore te feugait nulla facilisi.</p>
    </div>
    <p class="closing">Sincerely Your,</p>
    <p class="signature">Your Name</p>
  </section>

  <footer class="contact">
    <span class="contact-item">
      <svg viewBox="0 0 16 16" aria-hidden="true"><circle cx="8" cy="8" r="7" fill="none" stroke="var(--blue)" stroke-width="1.3"/><rect x="5.5" y="4" width="5" height="8" rx="1" fill="none" stroke="var(--blue)" stroke-width="1.2"/></svg>
      (555) 210-4471
    </span>
    <span class="contact-item">
      <svg viewBox="0 0 16 16" aria-hidden="true"><circle cx="8" cy="8" r="7" fill="none" stroke="var(--blue)" stroke-width="1.3"/><path d="M5 4.5 L6.5 4.5 L7.2 6.5 L6.2 7.3 C6.8 8.6 7.6 9.4 8.8 10 L9.6 9 L11.5 9.7 L11.5 11.2 C8 11.2 5 8.2 5 4.5 Z" fill="var(--blue)"/></svg>
      (555) 310-8890(Main)
    </span>
    <span class="contact-item">
      <svg viewBox="0 0 16 16" aria-hidden="true"><circle cx="8" cy="8" r="7" fill="none" stroke="var(--blue)" stroke-width="1.3"/><rect x="4" y="5" width="8" height="6" fill="none" stroke="var(--blue)" stroke-width="1.2"/><path d="M4 5 L8 8.5 L12 5" fill="none" stroke="var(--blue)" stroke-width="1.2"/></svg>
      jsmith@parcelwisehq.example
    </span>
    <span class="contact-divider"></span>
    <span class="contact-item">
      <svg viewBox="0 0 16 16" aria-hidden="true"><circle cx="8" cy="8" r="7" fill="none" stroke="var(--blue)" stroke-width="1.3"/><path d="M8 12.5 C6 10 5 8.6 5 7 A3 3 0 0 1 11 7 C11 8.6 10 10 8 12.5 Z" fill="var(--blue)"/></svg>
      27 Harbor Lane, Fairview, OR 97000
    </span>
  </footer>
</main>
</body>
</html>
```